Logistics Website Design

See website https://tqfreightglobal.com for theme and color details. Need the site to be re-done and reflect some of the designs shown in this list here: https://pixelvane.com/tags/logistics-company-website

Target Market(s)

Logistics & Transportation

Industry/Entity Type

Logistics and Supply Chain

Coding

Number of Pages Required

5+ page

Requirements
Must have
• Colors must match theme of logo. Looking for a sleek, interactive design.

```html
<!DOCTYPE html>
<html lang="en">
<head>
<meta charset="utf-8">
<title>TQ Freight Global — Delivering Strength In Every Mile</title>
<link href="https://fonts.googleapis.com/css2?family=Oswald:wght@500;600&family=Figtree:wght@400;500;600&display=swap" rel="stylesheet">
<style>
  :root {
    --orange: #e8592a;
    --orange-soft: #f0977a;
    --orange-pale: #f7c2ad;
    --ink: #161616;
    --ink-2: #1e1b1a;
    --white: #ffffff;
    --text-dim: #cfc7c3;
    --dusk-1: #2b3a4e;
    --dusk-2: #6a4a45;
    --dusk-3: #c66a3e;
  }
  * { box-sizing: border-box; margin: 0; padding: 0; }
  html, body { width: 1200px; height: 3057px; overflow: hidden; }
  body {
    position: relative;
    background: var(--ink);
    color: var(--white);
    font-family: "Figtree", Arial, sans-serif;
  }
  .abs { position: absolute; }
  .display {
    font-family: "Oswald", "Arial Narrow", sans-serif;
    font-weight: 500;
    text-transform: uppercase;
    letter-spacing: 0.5px;
    line-height: 1;
  }
  .center { left: 0; width: 1200px; text-align: center; }

  /* hero */
  .hero-art { left: 0; top: 0; width: 1200px; height: 760px; }
  .menu-toggle {
    left: 1061px; top: 62px; width: 52px; height: 52px; border-radius: 50%;
    background: var(--orange-pale); display: grid; place-items: center;
  }
  .brand { display: flex; align-items: center; justify-content: center; gap: 12px; }
  .brand-dot { width: 34px; height: 34px; border-radius: 50%; background: var(--orange); }
  .brand-name { font-family: "Figtree", Arial, sans-serif; font-weight: 600; font-size: 26px; letter-spacing: 2px; color: var(--white); }
  .hero-brand { top: 140px; }
  .hero-title-1 { top: 310px; font-size: 86px; color: var(--orange); }
  .hero-title-2 { top: 398px; font-size: 86px; color: var(--white); }
  .hero-sub { top: 494px; font-size: 20px; line-height: 33px; }
  .btn {
    display: flex; align-items: center; justify-content: center;
    border-radius: 24px; font-family: "Figtree", Arial, sans-serif; font-weight: 500;
  }
  .btn-primary { background: var(--orange); color: var(--white); }
  .btn-light { background: var(--white); color: var(--orange); }
  .hero-start { left: 366px; top: 582px; width: 232px; height: 47px; font-size: 16px; }
  .hero-contact { left: 628px; top: 582px; width: 206px; height: 47px; font-size: 16px; }

  /* about */
  .about-bg {
    left: 0; top: 770px; width: 1200px; height: 700px;
    background: radial-gradient(ellipse at 20% 40%, #2a2421 0%, var(--ink) 60%);
  }
  .about-art { left: 100px; top: 876px; width: 504px; height: 504px; }
  .section-title { font-size: 54px; color: var(--orange); }
  .about-title { left: 672px; top: 922px; }
  .about-copy {
    left: 672px; width: 416px; font-size: 16px; line-height: 28.5px;
    text-align: justify; color: var(--white);
  }
  .about-copy-1 { top: 990px; }
  .about-copy-2 { top: 1154px; }
  .about-more { left: 672px; top: 1294px; width: 142px; height: 41px; font-size: 15px; }

  /* services */
  .services-glow {
    left: 0; top: 1450px; width: 1200px; height: 650px;
    background: radial-gradient(ellipse at 50% 85%, rgba(200,90,50,0.35) 0%, rgba(22,22,22,0) 65%);
  }
  .services-title { top: 1496px; }
  .services-intro { left: 300px; top: 1561px; width: 600px; text-align: center; font-size: 17px; line-height: 28.5px; }
  .service-card {
    top: 1687px; width: 228px; height: 286px; border-radius: 20px;
    background: linear-gradient(180deg, rgba(70,38,28,0.75), rgba(48,28,22,0.55));
    text-align: center; padding: 34px 12px 0;
  }
  .service-card.is-active { border: 1px solid var(--orange); }
  .service-icon {
    width: 78px; height: 78px; border-radius: 50%; margin: 0 auto;
    background: radial-gradient(circle at 40% 35%, var(--orange-pale), var(--orange-soft) 70%, var(--orange));
  }
  .service-name { margin-top: 24px; font-size: 17px; color: var(--orange); font-weight: 500; }
  .service-text { margin-top: 8px; font-size: 14px; line-height: 24px; color: var(--text-dim); }

  /* contact */
  .contact-arc { left: 0; top: 2500px; width: 1200px; height: 200px; }
  .contact-panel {
    left: 160px; top: 2092px; width: 879px; height: 523px; border-radius: 48px;
    border: 2px solid var(--orange-pale);
    background: linear-gradient(160deg, #e3582b 0%, #e96238 45%, #d9542a 100%);
  }
  .contact-title { top: 2140px; font-size: 54px; color: var(--white); }
  .contact-sub { top: 2196px; font-size: 17px; line-height: 27px; }
  .field {
    background: var(--white); border-radius: 26px; color: #333;
    display: flex; align-items: center; gap: 14px; padding-left: 34px; font-size: 13px;
  }
  .field-name { left: 228px; top: 2284px; width: 357px; height: 50px; }
  .field-email { left: 228px; top: 2357px; width: 357px; height: 50px; }
  .field-phone { left: 228px; top: 2430px; width: 357px; height: 50px; }
  .field-comments { left: 614px; top: 2284px; width: 357px; height: 270px; align-items: flex-start; padding-top: 18px; }
  .send-btn {
    left: 228px; top: 2503px; width: 357px; height: 51px; border-radius: 26px;
    background: var(--ink); color: var(--white); font-size: 17px; font-weight: 600;
    display: flex; align-items: center; justify-content: center;
  }

  /* footer */
  .footer-brand { top: 2768px; }
  .footer-nav { top: 2896px; font-size: 16px; }
  .footer-nav span { position: absolute; transform: translateX(-50%); white-space: nowrap; }
  .social { top: 2937px; width: 32px; height: 32px; border-radius: 50%; background: var(--orange-pale); }
  .footer-rule { left: 176px; top: 2992px; width: 851px; height: 1px; background: #5a5552; }
  .copyright { top: 3012px; font-size: 13px; }
</style>
</head>
<body>

<!-- Hero -->
<svg class="abs hero-art" viewBox="0 0 1200 760" role="img" aria-label="Port at dusk with a container ship, stacked containers, a truck and a plane overhead">
  <defs>
    <linearGradient id="heroSky" x1="0" y1="0" x2="0" y2="1">
      <stop offset="0" stop-color="var(--dusk-1)"/>
      <stop offset="0.45" stop-color="var(--dusk-2)"/>
      <stop offset="0.75" stop-color="var(--dusk-3)"/>
      <stop offset="1" stop-color="#3a2a28"/>
    </linearGradient>
    <linearGradient id="heroBand" x1="0" y1="0" x2="1" y2="0">
      <stop offset="0" stop-color="#f29170"/>
      <stop offset="0.5" stop-color="#f6c5b0"/>
      <stop offset="1" stop-color="#f29170"/>
    </linearGradient>
  </defs>
  <path d="M0,500 Q600,970 1200,500 L1200,580 Q600,922 0,580 Z" fill="url(#heroBand)"/>
  <path d="M0,0 H1200 V500 Q600,970 0,500 Z" fill="url(#heroSky)"/>
  <path d="M0,0 H1200 V500 Q600,970 0,500 Z" fill="rgba(0,0,0,0.25)"/>
</svg>

<div class="abs menu-toggle" aria-label="Menu">
  <svg width="16" height="16" viewBox="0 0 16 16"><rect x="1" y="1" width="6" height="6" rx="2" fill="#161616"/><rect x="9" y="1" width="6" height="6" rx="2" fill="#161616"/><rect x="1" y="9" width="6" height="6" rx="2" fill="#161616"/><rect x="9" y="9" width="6" height="6" rx="2" fill="#161616"/></svg>
</div>

<div class="abs center brand hero-brand"><span class="brand-dot"></span><span class="brand-name">TQ FREIGHT GLOBAL</span></div>
<h1 class="abs center display hero-title-1">Delivering Strength</h1>
<div class="abs center display hero-title-2">In Every Mile</div>
<p class="abs center hero-sub">Precision logistics built from real-world experience - moving<br>complex freight with speed, reliability, and control.</p>
<a class="abs btn btn-primary hero-start">Start Your Shipment</a>
<a class="abs btn btn-light hero-contact">Contact Our Team</a>

<!-- Who we are -->
<div class="abs about-bg"></div>
<svg class="abs about-art" viewBox="0 0 504 504" role="img" aria-label="Warehouse worker with a glowing digital shelving overlay">
  <defs>
    <radialGradient id="aboutFill" cx="0.5" cy="0.45" r="0.6">
      <stop offset="0" stop-color="#6aa6d8"/>
      <stop offset="0.5" stop-color="#2d4f72"/>
      <stop offset="1" stop-color="#a8622f"/>
    </radialGradient>
    <linearGradient id="ringGrad" x1="0" y1="0" x2="1" y2="1">
      <stop offset="0" stop-color="#f7c2ad"/>
      <stop offset="1" stop-color="#e8592a"/>
    </linearGradient>
  </defs>
  <circle cx="252" cy="252" r="214" fill="url(#aboutFill)"/>
  <path d="M12,252 A240,240 0 0 1 300,16" fill="none" stroke="url(#ringGrad)" stroke-width="6"/>
  <path d="M318,20 A240,240 0 0 1 492,252" fill="none" stroke="url(#ringGrad)" stroke-width="10"/>
  <path d="M40,340 A230,230 0 0 0 464,340" fill="none" stroke="url(#ringGrad)" stroke-width="8"/>
  <path d="M318,20 V46" stroke="#f7c2ad" stroke-width="6"/>
</svg>
<h2 class="abs display section-title about-title">Who We Are</h2>
<p class="abs about-copy about-copy-1">TQ Freight Global™ was born out of real-world experience in the fitness equipment industry. What started as a company shipping strength equipment, cardio machines, and training gear to gyms, schools, and commercial facilities quickly evolved into something bigger.</p>
<p class="abs about-copy about-copy-2">As order volume grew and supply chains became more complex, the team developed deep expertise in coordinating freight, managing deliveries, and navigating the challenges of large-scale equipment transportation.</p>
<a class="abs btn btn-primary about-more">Explore More</a>

<!-- Services -->
<div class="abs services-glow"></div>
<h2 class="abs center display section-title services-title">Services We Offer</h2>
<p class="abs services-intro">We deliver a comprehensive range of open-deck and specialized transportation services - including flatbed, step deck, heavy haul, and over-dimensional freight solutions.</p>

<article class="abs service-card" style="left:112px">
  <div class="service-icon" role="img" aria-label="Flatbed truck illustration"></div>
  <h3 class="service-name">Flatbed Transportation</h3>
  <p class="service-text">From routine shipments to oversized and heavy-haul loads, we handle freight requiring proper..</p>
</article>
<article class="abs service-card is-active" style="left:361px">
  <div class="service-icon" role="img" aria-label="Step deck truck illustration"></div>
  <h3 class="service-name">Step Deck Transportation</h3>
  <p class="service-text">Our step deck trucking services support tall, heavy, and specialized freight that requires additional height..</p>
</article>
<article class="abs service-card" style="left:610px">
  <div class="service-icon" role="img" aria-label="Dry van truck illustration"></div>
  <h3 class="service-name">Dry Van Transportation</h3>
  <p class="service-text">From consumer goods to industrial materials, our dry van services provide the space, security..,</p>
</article>
<article class="abs service-card" style="left:859px">
  <div class="service-icon" role="img" aria-label="Heavy haul truck illustration"></div>
  <h3 class="service-name">Heavy Haul Transportation</h3>
  <p class="service-text">We provide heavy haul trucking solutions for oversized, overweight, &amp; over-dimensional freight.</p>
</article>

<!-- Contact -->
<svg class="abs contact-arc" viewBox="0 2500 1200 200" aria-hidden="true">
  <defs>
    <linearGradient id="arcGrad" x1="0" y1="0" x2="1" y2="0">
      <stop offset="0" stop-color="#f29170"/>
      <stop offset="0.5" stop-color="#f6b69c"/>
      <stop offset="1" stop-color="#f29170"/>
    </linearGradient>
  </defs>
  <path d="M0,2532 Q600,2700 1200,2532 L1200,2660 Q600,2470 0,2660 Z" fill="url(#arcGrad)"/>
</svg>
<section class="abs contact-panel" role="img" aria-label="Orange panel with a faint world map and logistics network backdrop"></section>
<h2 class="abs center display contact-title">We Move What Others Can’t</h2>
<p class="abs center contact-sub">TQ Freight Global™ delivers precision logistics<br>backed by real-world experience.</p>

<div class="abs field field-name">
  <svg width="12" height="13" viewBox="0 0 12 13"><circle cx="6" cy="3.5" r="3" fill="#222"/><path d="M0,13 Q0,7 6,7 Q12,7 12,13 Z" fill="#222"/></svg>Full Name
</div>
<div class="abs field field-email">
  <svg width="14" height="11" viewBox="0 0 14 11"><rect width="14" height="11" rx="1.5" fill="#222"/><path d="M1,1.5 L7,6 L13,1.5" stroke="#fff" stroke-width="1.3" fill="none"/></svg>Email Address
</div>
<div class="abs field field-phone">
  <svg width="12" height="12" viewBox="0 0 12 12"><path d="M2.5,0.5 L4.5,3 L3.3,4.4 Q4.6,7.2 7.6,8.7 L9,7.5 L11.5,9.5 L10.3,11.5 Q2.5,10.5 0.5,1.8 Z" fill="#222"/></svg>Contact Number
</div>
<div class="abs field field-comments">
  <svg width="15" height="12" viewBox="0 0 15 12"><path d="M1,5 Q1,1 7,1 Q13,1 13,5 Q13,9 7,9 L3,11 L4,8 Q1,7 1,5 Z" fill="none" stroke="#222" stroke-width="1.5"/></svg>Comments
</div>
<a class="abs send-btn">Send Message</a>

<!-- Footer -->
<div class="abs center brand footer-brand"><span class="brand-dot"></span><span class="brand-name">TQ FREIGHT GLOBAL</span></div>
<nav class="abs center footer-nav">
  <span style="left:296px">Home</span>
  <span style="left:413px">About Us</span>
  <span style="left:570px">Services We Offer</span>
  <span style="left:740px">Testimonials</span>
  <span style="left:887px">Contact Us</span>
</nav>
<a class="abs social" style="left:519px" aria-label="Social profile 1"></a>
<a class="abs social" style="left:562px" aria-label="Social profile 2"></a>
<a class="abs social" style="left:605px" aria-label="Social profile 3"></a>
<a class="abs social" style="left:648px" aria-label="Social profile 4"></a>
<div class="abs footer-rule"></div>
<p class="abs center copyright">(C) Copyright 2026 | All Rights Reserved</p>

</body>
</html>
```